Single-sided business card for restaurant velmora with new logo made on this site

Business card options with new logo including restaurant name, address, phone number and website. This business card is single-sided only and will be presented at the hostess desk for clients to take. I would like to see options based on a cream card background, a white card background, a yellow card background and a burgundy colored background. It needs to be elegant and traditional.

Target Market(s)

local and international crowd

Industry/Entity Type

restaurant

Contact Information for Business Card

address, website and phone number

Font styles to use
Serif

Colors
EE7325
F08F49
F5BC92
FAE3D3
FDF4ED

Requirements
Must have
• new logo, address, phone number, website
Should not have
• more than three colors

```html
<!DOCTYPE html>
<html lang="es">
<head>
<meta charset="utf-8">
<title>Velmora — Tarjeta de presentación</title>
<link rel="stylesheet" href="https://fonts.googleapis.com/css2?family=Cinzel:wght@500&family=Montserrat:wght@400;500&display=swap">
<style>
  :root {
    --backdrop: #2b2b2b;
    --card: #ffffff;
    --accent: #f08f49;
    --ink: #3a1f1c;
    --divider: #5a4a46;
  }
  * { margin: 0; padding: 0; box-sizing: border-box; }
  html, body {
    width: 1200px;
    height: 800px;
    overflow: hidden;
    background: var(--backdrop);
  }
  .card {
    position: absolute;
    left: 219px;
    top: 184px;
    width: 762px;
    height: 432px;
    background: var(--card);
    font-family: "Montserrat", sans-serif;
    color: var(--ink);
  }
  .card-frame {
    position: absolute;
    left: 22px;
    top: 19px;
    right: 22px;
    bottom: 19px;
    border: 4px solid var(--accent);
  }
  .brand {
    position: absolute;
    left: 137px;
    top: 135px;
    width: 200px;
    display: flex;
    flex-direction: column;
    align-items: center;
  }
  .brand-square {
    width: 93px;
    height: 93px;
    background: var(--accent);
  }
  .brand-name {
    margin-top: 14px;
    font-family: "Cinzel", serif;
    font-size: 30px;
    font-weight: 500;
    line-height: 36px;
    letter-spacing: 4px;
    padding-left: 4px;
    color: var(--ink);
  }
  .divider {
    position: absolute;
    left: 344px;
    top: 114px;
    width: 1px;
    height: 204px;
    background: var(--divider);
  }
  .details {
    position: absolute;
    left: 372px;
    top: 132px;
  }
  .address {
    font-style: normal;
    font-size: 17.5px;
    line-height: 21px;
  }
  .reservations-label {
    margin-top: 9px;
    font-size: 17.5px;
    line-height: 21px;
    padding-left: 2px;
  }
  .phone {
    margin-top: 4px;
    font-size: 23px;
    line-height: 28px;
    padding-left: 2px;
  }
  .website {
    margin-top: 6px;
    font-size: 16.5px;
    line-height: 20px;
    letter-spacing: 0.4px;
    padding-left: 2px;
  }
</style>
</head>
<body>
  <main class="card">
    <div class="card-frame"></div>

    <div class="brand">
      <div class="brand-square"></div>
      <div class="brand-name">VELMORA</div>
    </div>

    <div class="divider"></div>

    <section class="details">
      <address class="address">
        Restaurant Velmora<br>
        Jacarandá 418<br>
        Bahía Serena<br>
        Oaxaca CP 70140
      </address>
      <p class="reservations-label">Reservaciones</p>
      <p class="phone">958-555-0142</p>
      <p class="website">www.velmora.com.mx</p>
    </section>
  </main>
</body>
</html>
```